Web Design Project

Website Design Brief

Company Details
1a) Name of Company

MAPLEHAVEN
1) What is the nature of your business?: Briefly describe your products or services:

INDEPENDENT CONTEMPORARY TRADITIONAL ITALIAN RESTAURANT IN THE HEART OF ELMSWORTH QUAY ALSO CATERING FOR PRIVATE CORPORATE EVENTS AND WEDDING RECEPTIONS

1a) Who is your target market? Who are you hoping to reach with your site?

CITY CORPORATES, LOCAL CORPORATES/BUSINESSES, LOCAL RESIDENTS, VISITORS TO THE DOCK, LOCAL HOTELS

Website Details
1b) Do you have an existing website? If so, what is the URL?
HTTP://WWW.MAPLEHAVENTRATTORIA.EXAMPLE

2b) IMPORTANT: Please list at least 3 URLs (web addresses) of high quality sites that you like the look of (these do not have to be sites who’s business is similar to yours. It aids us in determining what your design style is.) Please consider layout, colours, navigation, graphics, and typography.

http://www.thecorvelle.example/

http://www.dunmorrow.example/

http://www.pavokitchen.example/

http://www.ilfaro.example/

3b) What colours or colour schemes would you like?

WHITE, BLACK, SILVER/ALUMINIUM (PLS LOOK AT OUR OUTSIDE CHAIRS)

4b) List the Navigation links for your Site:

5b) What type of look are you trying to achieve? (e.g. clean, high-tech, conservative, warm, flashy, etc.)

SIMPLE ELEGANT CLASSY INFORMATIVE, EASY TO USE, A REFLECTION OF THE BUSINESS ITSELF

6b) Please provide the addresses of competitors' sites, if possible:

Do not contact the client direct - all questions should go through Brightwell Venues - info@brightwellvenues.example
Updates

thanks for the designs that I have received so far. I have these general comments:

- please avoid using icons for phones or paperclips etc 
- use dummy text (one design used text from another website) 
- there won't any live social media feeds to the site
the client likes a lot of the designs that this company comes up with: 

i look forward to see some more designs

hi all, 

further to my last update, here are a few more pointers:
- there will be no search facilities - so no "search" box please 
- please just use the images supplied - no stock ones
- use just the page names give (no other pages) 

The client is looking for a simple, elegant design. 

Many thanks 
Rolf 

thanks for all the designs. 

I have uploaded another file to the brief which shows some posters that the client particularly likes. Perhaps the homepage could consist of large rectangle made up of a number of boxes - for some introductory text, a large image, mailing list, contact details, Lunch Special etc - just an idea! 
It's clear that the client likes clean lines with square edges. 
I want to be able to pass the designs directly onto the client so can designers avoid adding extra info or page. For example one design has a tab for a "Gift Card" - it will be easier for me if such additions are avoided. 

thanks!                                                                                                                                                                                                                                                                                                                                                                                                    

Thank you for all your designs - please keep them coming! 

hi all,

I am meeting the client tomorrow afternoon so please submit revisions / designs before then. 

Many thanks, 
Rolf

Target Market(s)

Business people, upmarket etc

Industry/Entity Type

Business

Requirements
Must have
• - The home page needs a slide show of images as well as:
- a mailing list form - very simple, "Join our mailing list - name, email"
- 3 or 4 sentences of text
- Friendpage link

```html
<!DOCTYPE html>
<html lang="en">
<head>
<meta charset="utf-8">
<title>Maplehaven Italian</title>
<link href="https://fonts.googleapis.com/css2?family=Sorts+Mill+Goudy:ital@0;1&display=swap" rel="stylesheet">
<style>
  :root {
    --bg: #1e1e1e;
    --rule: #474747;
    --rule-soft: #353535;
    --silver: #c4c7cb;
    --silver-deep: #9da1a6;
    --field: #333333;
    --text: #f4f4f4;
    --muted: #8a8a8a;
  }
  * { box-sizing: border-box; margin: 0; padding: 0; }
  html, body { width: 1200px; height: 750px; overflow: hidden; background: var(--bg); }
  body { position: relative; font-family: "Sorts Mill Goudy", Georgia, serif; color: var(--text); }

  .hero {
    position: absolute; left: 360px; top: 0; width: 840px; height: 750px;
    background:
      radial-gradient(ellipse at 55% 70%, rgba(240,190,140,0.45), transparent 45%),
      radial-gradient(ellipse at 80% 60%, rgba(230,200,180,0.35), transparent 40%),
      linear-gradient(180deg, #6d5a52 0%, #5a3a2c 35%, #4a2a1c 60%, #2a1710 100%);
  }
  .hero-fade {
    position: absolute; left: 360px; top: 0; width: 160px; height: 750px;
    background: linear-gradient(90deg, var(--bg) 0%, rgba(30,30,30,0.6) 45%, rgba(30,30,30,0) 100%);
  }

  .reserve-badge {
    position: absolute; left: 895px; top: 0; width: 116px; height: 62px;
    background: var(--silver-deep);
    display: flex; flex-direction: column; justify-content: center; align-items: center;
    font-style: italic; font-size: 18px; line-height: 15px; color: #fff;
  }

  .sidebar { position: absolute; left: 34px; top: 18px; width: 273px; }
  .brand {
    border-top: 2px solid var(--rule); border-bottom: 2px solid var(--rule);
    height: 91px; display: flex; align-items: center; justify-content: center;
    font-size: 34px; color: #fff; letter-spacing: 1px;
  }
  .nav { list-style: none; border-bottom: 2px solid var(--rule); }
  .nav li {
    height: 38.7px; border-bottom: 1px solid var(--rule-soft);
    display: flex; align-items: center; font-size: 14px;
  }
  .nav li:last-child { border-bottom: none; }
  .nav svg { margin: 0 9px 0 18px; }
  .nav .active { color: var(--silver); }

  .newsletter-title { margin: 14px 0 0 7px; font-style: italic; font-size: 14px; color: var(--silver); }
  .newsletter-form { margin: 6px 0 0 6px; }
  .form-row { display: flex; align-items: center; }
  .form-row + .form-row { margin-top: 6px; }
  .field {
    width: 200px; height: 30px; background: var(--field);
    font-family: Arial, sans-serif; font-size: 9px; color: var(--muted);
    padding-left: 13px; display: flex; align-items: center;
  }
  .submit-link { margin-left: 13px; font-style: italic; font-size: 15px; color: #fff; text-decoration: underline; }

  .promo {
    margin-top: 14px; margin-left: -2px; width: 275px; height: 154px;
    border: 2px solid var(--rule); text-align: center; padding-top: 6px;
  }
  .promo h2 { font-weight: normal; font-style: italic; font-size: 19px; color: var(--silver); }
  .promo p {
    font-family: Arial, sans-serif; font-size: 8.6px; line-height: 15px; color: #fff;
    text-align: left; padding: 0 12px 0 25px; margin-top: 3px;
  }
  .promo p + p { margin-top: 15px; }
  .read-more {
    display: inline-block; margin-top: 12px; width: 87px; height: 25px; line-height: 25px;
    background: var(--silver-deep); color: #fff; font-size: 12px;
  }

  .follow { margin: 13px 0 0 19px; display: flex; align-items: center; font-size: 14px; }
  .follow em { color: #fff; margin-right: 12px; }
  .follow .social { color: var(--silver); font-size: 15px; }
  .follow .divider { width: 1px; height: 13px; background: #555; margin: 0 9px; }
</style>
</head>
<body>
  <div class="hero" role="img" aria-label="Photograph of the lounge interior with white leather sofas, glass tables, candles and windows onto the quay"></div>
  <div class="hero-fade"></div>

  <div class="reserve-badge"><span>Reservation</span><span>Online</span></div>

  <aside class="sidebar">
    <div class="brand">Maplehaven</div>
    <ul class="nav">
      <li><svg width="13" height="6" viewBox="0 0 13 6"><path d="M0 3H12M9 0.5L12 3L9 5.5" stroke="#888" fill="none"/></svg>Home</li>
      <li><svg width="13" height="6" viewBox="0 0 13 6"><path d="M0 3H12M9 0.5L12 3L9 5.5" stroke="#888" fill="none"/></svg>Our Restaurant</li>
      <li><svg width="13" height="6" viewBox="0 0 13 6"><path d="M0 3H12M9 0.5L12 3L9 5.5" stroke="#888" fill="none"/></svg>Our Menu</li>
      <li class="active"><svg width="13" height="6" viewBox="0 0 13 6"><path d="M0 3H12M9 0.5L12 3L9 5.5" stroke="#888" fill="none"/></svg>Gallery</li>
      <li><svg width="13" height="6" viewBox="0 0 13 6"><path d="M0 3H12M9 0.5L12 3L9 5.5" stroke="#888" fill="none"/></svg>Events</li>
      <li><svg width="13" height="6" viewBox="0 0 13 6"><path d="M0 3H12M9 0.5L12 3L9 5.5" stroke="#888" fill="none"/></svg>Reservations</li>
      <li><svg width="13" height="6" viewBox="0 0 13 6"><path d="M0 3H12M9 0.5L12 3L9 5.5" stroke="#888" fill="none"/></svg>Contact Us</li>
    </ul>

    <div class="newsletter-title">Newsletter</div>
    <div class="newsletter-form">
      <div class="form-row"><div class="field">Enter your name</div></div>
      <div class="form-row">
        <div class="field">Enter you email</div>
        <span class="submit-link">Submit</span>
      </div>
    </div>

    <section class="promo">
      <h2>Our Promotions</h2>
      <p>But I must explain to you how all this mistaken idea of denouncing pleasure and praising pain was borm</p>
      <p>and expound the actual teachings of the great explorer of the truth, the master-builder of human happiness.</p>
      <span class="read-more">Read More</span>
    </section>

    <div class="follow">
      <em>Follow us:</em>
      <span class="social">Friendpage</span>
      <span class="divider"></span>
      <span class="social">Chirper</span>
    </div>
  </aside>
</body>
</html>
```